A clean crisp business card for a Landscape Construction company. Designed to be easy to read contact/ info and also be appealing/interesting, unlike a traditional business card.

Industry/Entity Type

Landscape Construction

Contact Information for Business Card

Company name : Brambleford Landscape Construction, phone number: (877) 62Vista, website:Bramblefordyards.example, Email, sales@bramblefordyards.example

Requirements
Nice to have
• Luxurious finishes/ details…. Icons or emblems next to contact info
Should not have
• Clipart or general pictures

```html
<!DOCTYPE html>
<html lang="en">
<head>
<meta charset="utf-8">
<title>Brambleford Landscape Construction – Business Card</title>
<link rel="stylesheet" href="https://fonts.googleapis.com/css2?family=Cinzel:wght@500;600&family=Open+Sans:wght@400;600&display=swap">
<style>
  :root {
    --page-bg: #d4d6d8;
    --card-bg: #262626;
    --card-bg-light: #2e2e2e;
    --brand-blue: #2a6fc0;
    --brand-green: #9ccc3c;
    --silver: #8a8a8a;
    --text-light: #f2f2f2;
  }
  * { margin: 0; padding: 0; box-sizing: border-box; }
  html, body {
    width: 1200px; height: 928px; overflow: hidden;
    background: var(--page-bg);
  }
  .card {
    position: absolute;
    border-radius: 16px;
    overflow: hidden;
    background: radial-gradient(ellipse at 50% 40%, var(--card-bg-light), var(--card-bg) 70%);
  }
  .card--front { left: 267px; top: 59px; width: 670px; height: 382px; }
  .card--back  { left: 264px; top: 484px; width: 676px; height: 387px; }

  .brand-dot {
    display: block;
    width: 46px; height: 46px; border-radius: 50%;
    background: var(--silver);
  }

  /* front */
  .front-brand {
    position: absolute; left: 0; width: 670px; top: 118px;
    display: flex; flex-direction: column; align-items: center; gap: 18px;
    text-align: center;
  }
  .front-brand .brand-name {
    display: block; width: 100%;
    font-family: "Cinzel", serif; font-weight: 600;
    font-size: 30px; line-height: 1.35; letter-spacing: 1px;
    color: var(--silver); text-align: center;
  }
  .front-url {
    position: absolute; left: 0; width: 670px; top: 333px; text-align: center;
    font-family: "Cinzel", serif; font-weight: 600; font-size: 15px;
    letter-spacing: 2px; color: var(--brand-blue);
  }
  .front-url .domain { color: var(--brand-green); }

  /* back */
  .person { position: absolute; left: 41px; top: 48px; }
  .person-name {
    font-family: "Cinzel", serif; font-weight: 600; font-size: 28px;
    letter-spacing: 1px; color: var(--brand-blue);
  }
  .person-name .surname { color: var(--brand-green); }
  .person-role {
    font-family: "Open Sans", sans-serif; font-size: 15px;
    color: var(--text-light); margin-top: 6px;
  }
  .back-brand {
    position: absolute; left: 396px; width: 262px; top: 66px;
    display: flex; flex-direction: column; align-items: center; gap: 10px;
    text-align: center;
  }
  .back-brand .brand-dot { background: var(--brand-blue); width: 40px; height: 40px; }
  .back-brand .brand-name {
    display: block; width: 100%;
    font-family: "Cinzel", serif; font-weight: 600; font-size: 20px;
    line-height: 1.3; color: var(--brand-blue); text-align: center;
  }
  .contact-list {
    position: absolute; left: 41px; top: 196px; list-style: none;
    font-family: "Open Sans", sans-serif; font-size: 15.5px; color: var(--text-light);
  }
  .contact-list li {
    display: flex; align-items: center; gap: 8px; height: 32px;
  }
  .contact-list svg { width: 17px; height: 17px; fill: var(--brand-green); flex: none; }
  .contact-list .phone { letter-spacing: 1px; }
  .wave { position: absolute; left: 0; top: 0; width: 676px; height: 387px; }
  .address {
    position: absolute; right: 32px; top: 308px; text-align: right;
    font-family: "Open Sans", sans-serif; font-weight: 600; font-size: 15.5px;
    font-style: normal; line-height: 27px; color: #ffffff;
  }
</style>
</head>
<body>

<section class="card card--front">
  <div class="front-brand">
    <span class="brand-dot"></span>
    <span class="brand-name">Brambleford<br>Landscape Construction</span>
  </div>
  <p class="front-url">www.<span class="domain">Bramblefordyards</span>.example</p>
</section>

<section class="card card--back">
  <svg class="wave" viewBox="0 0 676 387" aria-hidden="true">
    <path d="M0 266 C70 322 140 360 240 356 C380 350 520 246 676 262 L676 387 L0 387 Z" fill="#000" opacity="0.6"/>
    <path d="M0 268 C70 324 140 358 240 354 C380 348 520 244 676 262 L676 387 L0 387 Z" fill="var(--brand-green)"/>
    <path d="M0 276 C70 330 140 360 240 354 C380 346 520 258 676 276 L676 387 L0 387 Z" fill="#1e1e1e"/>
    <path d="M0 280 C70 334 140 363 240 357 C380 349 520 262 676 280 L676 387 L0 387 Z" fill="var(--brand-blue)"/>
  </svg>

  <div class="person">
    <h1 class="person-name">Ellis <span class="surname">Harper</span></h1>
    <p class="person-role">Director</p>
  </div>

  <div class="back-brand">
    <span class="brand-dot"></span>
    <span class="brand-name">Brambleford<br>Landscape Construction</span>
  </div>

  <ul class="contact-list">
    <li class="phone">
      <svg viewBox="0 0 24 24"><path d="M6.6 10.8a15.1 15.1 0 0 0 6.6 6.6l2.2-2.2a1 1 0 0 1 1-.25 11.4 11.4 0 0 0 3.6.57 1 1 0 0 1 1 1V20a1 1 0 0 1-1 1A17 17 0 0 1 3 4a1 1 0 0 1 1-1h3.5a1 1 0 0 1 1 1c0 1.25.2 2.45.57 3.57a1 1 0 0 1-.25 1z"/></svg>
      (877) 62Vista
    </li>
    <li>
      <svg viewBox="0 0 24 24"><path d="M2 5h20v2l-10 6L2 7z"/><path d="M2 9l10 6 10-6v10H2z"/></svg>
      sales@bramblefordyards.example
    </li>
    <li>
      <svg viewBox="0 0 24 24"><circle cx="12" cy="12" r="10"/><path d="M7 8c2 0 3 1 3 3s-2 2-2 4M15 5c-1 2 1 3 2 4s0 3 2 4" stroke="#262626" stroke-width="1.6" fill="none"/></svg>
      www.bramblefordyards.example
    </li>
  </ul>

  <address class="address">
    4120 Larkmoor Valley Rd<br>
    Suite 310, Fernhill, OH 45990
  </address>
</section>

</body>
</html>
```